Business card for law firm

Need business card for new law firm. Think confident, authoritative, conservative, but not stuffy or old-fashioned.

Contact Information for Business Card

Content for card - logo (uploaded), plus the following:

Paul Whitcombe (larger font)
Managing Partner (larger font, but not as large as name)
Level 9, 7 Ferris Lane
Sydney NSW 2000
Main Tel 02 9364 2710
Direct Tel 02 8472 3159
Email paul@qvlegal.com.au
www.qvlegal.com.au

Letterhead design should include logo plus:
Level 9, 7 Ferris Lane
Sydney NSW 2000
Tel 02 8472 3159
www.qvlegal.com.au

```html
<!DOCTYPE html>
<html lang="en">
<head>
<meta charset="utf-8">
<title>Quayvale Legal – Business Card</title>
<link href="https://fonts.googleapis.com/css2?family=Open+Sans:wght@400;600;700&display=swap" rel="stylesheet">
<style>
  :root{
    --stage:#d3d4d7;
    --stage-light:#ececec;
    --card:#ffffff;
    --navy:#001c58;
    --ink:#111111;
    --rule:#000000;
    --watermark:#e6e8ee;
    --edge:#9a9a9a;
  }
  *{box-sizing:border-box;margin:0;padding:0}
  html,body{width:1200px;height:1080px;overflow:hidden}
  body{
    position:relative;
    background:linear-gradient(135deg,var(--stage-light) 0%,var(--stage) 60%,#c6c7ca 100%);
    font-family:"Open Sans",Arial,sans-serif;
    color:var(--ink);
  }
  .card{
    position:absolute;
    background:var(--card);
    border:1px solid var(--edge);
    border-radius:26px;
    overflow:hidden;
  }
  /* Front card */
  .card--front{left:368px;top:78px;width:779px;height:446px}
  .watermark-block{
    position:absolute;right:0;top:0;width:203px;height:240px;
    background:var(--watermark);
  }
  .brand{position:absolute;text-align:center;color:var(--ink);font-weight:400}
  .brand__mark{display:block;background:var(--navy);margin:0 auto}
  .brand__name{display:block;text-transform:uppercase;line-height:1}
  .card--front .brand{left:30px;top:18px;width:320px}
  .card--front .brand__mark{width:74px;height:74px}
  .card--front .brand__name--main{font-size:42px;letter-spacing:4px;margin-top:38px}
  .card--front .brand__name--sub{font-size:16px;letter-spacing:17px;margin-top:12px;padding-left:17px}
  .address{
    position:absolute;left:36px;top:240px;
    font-size:19.5px;color:#222;
  }
  .rule{position:absolute;left:0;right:0;top:276px;height:5px;background:var(--rule)}
  .band{
    position:absolute;left:0;right:0;top:284px;bottom:0;
    background:var(--navy);color:#fff;
  }
  .notch{position:absolute;left:106px;top:280px;width:36px;height:18px}
  .person{position:absolute;left:39px;top:48px}
  .person__name{font-weight:700;font-size:26px;letter-spacing:.3px}
  .person__role{font-size:19.5px;margin-top:6px;letter-spacing:.3px}
  .contacts{position:absolute;left:326px;top:16px;list-style:none}
  .contacts li{display:flex;align-items:center;font-size:19.5px;height:34.5px}
  .contacts svg{width:18px;height:18px;margin-right:8px;flex:none}
  /* Back card */
  .card--back{left:71px;top:578px;width:780px;height:446px}
  .card--back .brand{left:0;right:0;top:56px}
  .card--back .brand__mark{width:94px;height:94px}
  .card--back .brand__name--main{font-size:52px;letter-spacing:5px;margin-top:62px}
  .card--back .brand__name--sub{font-size:20px;letter-spacing:22px;margin-top:14px;padding-left:22px}
  .web{
    position:absolute;left:0;right:0;top:366px;text-align:center;
    font-size:24px;letter-spacing:4px;color:#222;
  }
  .web strong{color:var(--navy);font-weight:700}
</style>
</head>
<body>

<section class="card card--front" aria-label="Business card front">
  <div class="watermark-block" aria-hidden="true"></div>
  <div class="brand">
    <span class="brand__mark" aria-hidden="true"></span>
    <span class="brand__name brand__name--main">Quayvale</span>
    <span class="brand__name brand__name--sub">Legal</span>
  </div>
  <p class="address">Level 9, 7 Ferris Lane, Sydney NSW 2000</p>
  <div class="rule"></div>
  <div class="band">
    <div class="person">
      <p class="person__name">PAUL WHITCOMBE</p>
      <p class="person__role">MANAGING PARTNER</p>
    </div>
    <ul class="contacts">
      <li><svg viewBox="0 0 20 20"><circle cx="10" cy="10" r="8.5" fill="none" stroke="#fff" stroke-width="1.5"/><path d="M7 5.5c-1 1-1 3 .5 5.5s3.5 4 5 4l1.2-1.6-2-1.4-1 .8c-1-.6-2-2-2.4-3l1-.8-.9-2.2z" fill="#fff"/></svg>02 9364 2710(Main)</li>
      <li><svg viewBox="0 0 20 20"><circle cx="10" cy="10" r="8.5" fill="none" stroke="#fff" stroke-width="1.5"/><path d="M7 5.5c-1 1-1 3 .5 5.5s3.5 4 5 4l1.2-1.6-2-1.4-1 .8c-1-.6-2-2-2.4-3l1-.8-.9-2.2z" fill="#fff"/></svg>02 8472 3159(Direct)</li>
      <li><svg viewBox="0 0 20 20"><path d="M2 8l8-5 8 5v8H2z" fill="#fff"/><path d="M2 8l8 5 8-5" fill="none" stroke="#001c58" stroke-width="1.4"/></svg>paul@qvlegal.com.au</li>
      <li><svg viewBox="0 0 20 20" fill="none" stroke="#fff" stroke-width="1.3"><circle cx="10" cy="10" r="8"/><ellipse cx="10" cy="10" rx="3.5" ry="8"/><path d="M2 10h16M3.5 6h13M3.5 14h13"/></svg>www.qvlegal.com.au</li>
    </ul>
  </div>
  <svg class="notch" viewBox="0 0 36 18" aria-hidden="true"><path d="M0 0h36L18 16z" fill="#000"/><path d="M6 2h24L18 12z" fill="#001c58"/></svg>
</section>

<section class="card card--back" aria-label="Business card back">
  <div class="brand">
    <span class="brand__mark" aria-hidden="true"></span>
    <span class="brand__name brand__name--main">Quayvale</span>
    <span class="brand__name brand__name--sub">Legal</span>
  </div>
  <p class="web">www.<strong>qvlegal</strong>.com.au</p>
</section>

</body>
</html>
```